Web Design Project for a new download application :-)

We need a website design and a logo design for a new website and desktop application.
The Website will be www.Gruvlo.com
The installed application will be: Gruvlo

Gruvlo is a desktop application that searches and finds all kind of Media files (Movies, Games, Songs, software, etc..)
Gruvlo will also manage the download process for the selected files.
Gruvlo automates the whole search and download process.

User Flow:
users will initially visit the website.
user will download the application from the website
user will install the application on his computer.
user will run and use the application.

What makes our software special:
-Great search engine for searching media files.
-Very high speed downloads. maximum speeds.
-Allow used to Search by: file type, size, date, format
-Pause and resume downloads
-Get any file you want instantly.
-Unlimited Downloads.

We will need:
Logo
WebSite Design
Icons for the desktop application.

we need only PSDs - no codded pages are needed !

Design to the following screen Size & resolution: 1024 x 768

Target Market(s)

movies and music lovers.
users who download movies, games, softwares, music etc...

Industry/Entity Type

Software

Requirements
Must have
• must have download button

```html
<!DOCTYPE html>
<html lang="en">
<head>
<meta charset="utf-8">
<title>Gruvlo – Download all kind of media files</title>
<link href="https://fonts.googleapis.com/css2?family=Ubuntu:wght@400;500;700&family=Open+Sans:wght@400;600&family=Roboto+Condensed:wght@400&display=swap" rel="stylesheet">
<style>
  :root {
    --hero-deep: #0a2a8c;
    --hero-mid: #1550c8;
    --hero-light: #3d8df0;
    --white: #ffffff;
    --page-bg: #f4f4f4;
    --feature-blue: #1a7fd0;
    --body-grey: #555555;
    --quote-grey: #444444;
    --mark-grey: #c4c4c4;
    --rule-grey: #dcdcdc;
    --ribbon-orange: #f7931e;
    --ribbon-dark: #d46a00;
    --accent-orange: #e8780f;
    --btn-yellow-top: #ffd34a;
    --btn-yellow-bottom: #f5a300;
    --btn-text: #1a1a1a;
    --footer-blue: #1d86dc;
  }
  * { box-sizing: border-box; margin: 0; padding: 0; }
  html, body { width: 1200px; height: 1037px; overflow: hidden; }
  body { position: relative; background: var(--page-bg); font-family: "Open Sans", Arial, sans-serif; }

  .rainbow-bar { position: absolute; left: 0; top: 0; width: 1200px; height: 7px;
    background: linear-gradient(90deg, #f7a21b, #f4e31b, #5cc23a, #1aa0e0, #7b3fc4, #e0249a, #f04a1a); }

  .hero { position: absolute; left: 0; top: 7px; width: 1200px; height: 407px;
    background: radial-gradient(ellipse 60% 90% at 55% 35%, var(--hero-light) 0%, var(--hero-mid) 45%, var(--hero-deep) 100%); }

  .brand { position: absolute; font-family: "Ubuntu", sans-serif; font-weight: 700; color: var(--white); letter-spacing: -1px; line-height: 1; }
  .brand--header { left: 105px; top: 30px; font-size: 68px; }
  .brand--footer { left: 912px; top: 956px; font-size: 56px; }

  .main-nav { position: absolute; top: 45px; left: 519px; display: flex; align-items: center; font-family: "Ubuntu", sans-serif; font-size: 17px; text-transform: uppercase; line-height: 1; }
  .main-nav a { color: var(--white); text-decoration: none; margin-right: 17px; }
  .main-nav a.is-active { background: linear-gradient(#fff, #dcdcdc); color: #222; padding: 7px 10px; border-radius: 3px; box-shadow: 0 2px 4px rgba(0,0,0,.35); }

  .language { position: absolute; left: 912px; top: 49px; display: flex; align-items: center; font-size: 13px; color: var(--white); }
  .language__box { margin-left: 6px; width: 75px; height: 22px; background: var(--white); color: #222; font-size: 13px; padding: 2px 5px; position: relative; }
  .language__box::after { content: ""; position: absolute; right: 5px; top: 9px; border: 4px solid transparent; border-top-color: #222; }

  .device-showcase { position: absolute; left: 104px; top: 121px; width: 519px; height: 320px; border-radius: 10px;
    background: linear-gradient(180deg, #1b1f2c 0%, #2f3546 60%, #cfd3d8 90%, #e4e6e9 100%); }

  .headline { position: absolute; left: 640px; color: var(--white); font-family: "Ubuntu", sans-serif; line-height: 1; white-space: nowrap; }
  .headline--big { top: 130px; font-size: 73px; font-weight: 700; letter-spacing: -1px; }
  .headline--sub { top: 205px; left: 641px; font-size: 35px; font-weight: 700; }
  .headline--list { top: 246px; left: 643px; font-family: "Roboto Condensed", sans-serif; font-size: 25px; }

  .download-btn { position: absolute; left: 644px; top: 284px; width: 326px; height: 73px; border-radius: 4px;
    background: linear-gradient(var(--btn-yellow-top), var(--btn-yellow-bottom)); border: 1px solid #c98400;
    font-family: "Ubuntu", sans-serif; font-weight: 700; font-size: 32px; color: var(--btn-text);
    display: flex; align-items: center; justify-content: center; text-decoration: none; box-shadow: 0 2px 6px rgba(0,0,0,.3); }

  .section-ribbon { position: absolute; left: 105px; top: 458px; }
  .section-ribbon__label { position: absolute; left: 22px; top: 0; font-family: "Ubuntu", sans-serif; font-size: 36px; color: var(--white); line-height: 46px; }

  .feature-list { position: absolute; left: 130px; top: 520px; width: 932px; display: flex; }
  .feature { width: 233px; text-align: center; padding: 0 14px; border-left: 1px solid #e6e6e6; }
  .feature:first-child { border-left: none; }
  .feature__icon { height: 70px; display: flex; justify-content: center; align-items: center; }
  .feature__title { margin: 6px -8px 0; font-family: "Ubuntu", sans-serif; font-weight: 400; font-size: 18.5px; line-height: 22px; color: var(--feature-blue); }
  .feature__text { margin-top: 7px; font-size: 12.5px; line-height: 18px; color: var(--body-grey); }

  .carousel-arrow { position: absolute; top: 620px; }
  .carousel-arrow--prev { left: 110px; }
  .carousel-arrow--next { left: 1060px; }

  .divider { position: absolute; left: 205px; top: 764px; width: 815px; height: 1px; background: var(--rule-grey); }

  .testimonial__mark { position: absolute; font-family: Georgia, serif; font-size: 96px; font-weight: 700; color: var(--mark-grey); line-height: 1; }
  .testimonial__mark--open { left: 116px; top: 770px; }
  .testimonial__mark--close { left: 1044px; top: 852px; }
  .testimonial__text { position: absolute; left: 170px; top: 789px; width: 870px; font-size: 12.3px; line-height: 18px; color: var(--quote-grey); }
  .testimonial__author { position: absolute; left: 172px; top: 867px; font-size: 12px; color: #333; }
  .testimonial__author span { color: var(--accent-orange); }

  .site-footer { position: absolute; left: 0; top: 937px; width: 1200px; height: 100px; background: var(--footer-blue); color: var(--white); }
  .footer-nav { position: absolute; left: 117px; top: 28px; font-size: 12.5px; }
  .footer-nav a { color: var(--white); margin-right: 12px; }
  .footer-contact { position: absolute; left: 117px; top: 54px; font-size: 13.5px; }
  .footer-contact a { color: var(--white); }
</style>
</head>
<body>
  <div class="rainbow-bar"></div>

  <header class="hero"></header>

  <div class="brand brand--header">Gruvlo</div>

  <nav class="main-nav">
    <a class="is-active" href="#">Home</a>
    <a href="#">Download</a>
    <a href="#">Support</a>
    <a href="#">Affiliates</a>
  </nav>

  <div class="language">Select Language <div class="language__box">English</div></div>

  <div class="device-showcase" role="img" aria-label="Desktop monitor and laptop showing the Gruvlo file browser with photo thumbnails"></div>

  <h1 class="headline headline--big">DOWNLOAD</h1>
  <div class="headline headline--sub">ALL KIND OF MEDIA FILES</div>
  <div class="headline headline--list">MOVIES, GAMES, SONGS, SOFTWARE, ETC.</div>

  <a class="download-btn" href="#">DOWNLOAD Gruvlo</a>

  <div class="section-ribbon">
    <svg width="240" height="56" viewBox="0 0 240 56">
      <polygon points="0,0 228,0 240,25 226,48 0,48" fill="var(--ribbon-orange)"/>
      <polygon points="0,48 11,48 11,56" fill="var(--ribbon-dark)"/>
    </svg>
    <div class="section-ribbon__label">Features</div>
  </div>

  <svg class="carousel-arrow carousel-arrow--prev" width="22" height="30" viewBox="0 0 22 30"><polyline points="18,2 5,15 18,28" fill="none" stroke="#111" stroke-width="6"/></svg>
  <svg class="carousel-arrow carousel-arrow--next" width="22" height="30" viewBox="0 0 22 30"><polyline points="4,2 17,15 4,28" fill="none" stroke="#111" stroke-width="6"/></svg>

  <section class="feature-list">
    <article class="feature">
      <div class="feature__icon">
        <svg width="70" height="70" viewBox="0 0 70 70"><circle cx="28" cy="28" r="22" fill="#cfe6fb" stroke="#7aa6cf" stroke-width="4"/><line x1="44" y1="44" x2="64" y2="64" stroke="#f0a020" stroke-width="9" stroke-linecap="round"/></svg>
      </div>
      <h3 class="feature__title">Great Search Engine for Searching Media Files</h3>
      <p class="feature__text">Lorem ipsum dolor sit amet, consectetur adipiscing elit. Sed mollis, ante placerat placerat varius, elit ante varius quam, sit amet dignissim purus urna vel</p>
    </article>
    <article class="feature">
      <div class="feature__icon">
        <svg width="66" height="66" viewBox="0 0 66 66"><circle cx="33" cy="33" r="30" fill="#f07a10" stroke="#eee" stroke-width="4"/><path d="M33 16 V42 M22 32 L33 44 L44 32" fill="none" stroke="#fff" stroke-width="6" stroke-linecap="round" stroke-linejoin="round"/></svg>
      </div>
      <h3 class="feature__title">Very High Speed Downloads</h3>
      <p class="feature__text">Curabitur convallis lectus quis tellus suscipit sollicitudin. Phasellus suscipit justo sit amet nisl rhoncus congue. Integer non egestas nibh.</p>
    </article>
    <article class="feature">
      <div class="feature__icon">
        <svg width="64" height="54" viewBox="0 0 64 54"><rect x="2" y="2" width="40" height="44" rx="3" fill="#f2f2f2" stroke="#999" stroke-width="2"/><path d="M9 14h26M9 22h26M9 30h20" stroke="#888" stroke-width="3"/><path d="M42 26 h10 v10 h8 l-13 14 l-13 -14 h8z" fill="#5cbf2a"/></svg>
      </div>
      <h3 class="feature__title">Search by: file type, size,<br>date, format</h3>
      <p class="feature__text">Nulla vitae imperdiet elit. Quisque vehicula, nulla sit amet ultrices molestie, purus tortor consequat magna, et eleifend elit quam</p>
    </article>
    <article class="feature">
      <div class="feature__icon">
        <svg width="52" height="52" viewBox="0 0 52 52"><circle cx="26" cy="26" r="24" fill="#1a3fc4"/><rect x="17" y="15" width="6" height="22" fill="#fff"/><rect x="29" y="15" width="6" height="22" fill="#fff"/></svg>
      </div>
      <h3 class="feature__title">Pause and Resume Downloads</h3>
      <p class="feature__text">Mauris eu quam sit amet sem suscipit rhoncus. Ut mauris dolor, bibendum at lacinia sit amet, dictum a justo. Aliquam ac est nunc, in suscipit libero.</p>
    </article>
  </section>

  <div class="divider"></div>

  <blockquote class="testimonial">
    <div class="testimonial__mark testimonial__mark--open">“</div>
    <p class="testimonial__text">Aenean nunc dui, varius vitae auctor eu, tincidunt adipiscing sem. Praesent massa nibh, imperdiet eget luctus vel, suscipit sit amet augue. Donec risus lacus, luctus nec condimentum non, venenatis eu risus. Vestibulum lorem nunc, placerat nec blandit at, mollis a justo. In faucibus lacus a magna congue id auctor lectus tristique. Aenean imperdiet bibendum est, ut accumsan neque bibendum quis. Quisque non enim eget lacus hendrerit faucibus. Nullam est erat, posuere vitae sodales</p>
    <div class="testimonial__author"><span>Dana Corliss</span> &nbsp;|&nbsp; Perth</div>
    <div class="testimonial__mark testimonial__mark--close">”</div>
  </blockquote>

  <footer class="site-footer">
    <nav class="footer-nav">
      <a href="#">HOME</a> <a href="#">DOWNLOAD</a> <a href="#">SUPPORT</a> <a href="#">AFFILIATES</a>
    </nav>
    <div class="footer-contact">email : <a href="#">contact@gruvlo.com</a> &nbsp;| &nbsp;Call us - 0198765432 &nbsp;| &nbsp;©2011 Gruvlo. All rights reserved</div>
  </footer>
  <div class="brand brand--footer">Gruvlo</div>
</body>
</html>
```